Brightwick Music Studio needs a promotional postcard design

We are looking for a postcard design for a small business that provides clients with private music lesson instruction. We are looking for a design that will convey the message of "music is fun for kids" that will appeal to parents and encourage them to sign up. We have a company logo that should be used and our color scheme is teal and turquoise. All of our contact info should be displayed as well.

Target Market(s)

Parents with young kids

Contact Information for Business Card

web: www.brightwickmusicstudio.example
email: lessons@brightwickmusicstudio.example
phone: 202-555-0147

Font styles to use
Serif
Sans Serif

Colors
33b8a4
86cfc6
0456a4
87cfc6

Requirements
Must have
• Music lessons in your home
• Creating little stars one at a time
• Sign Up Now
• Please use these images:
Nice to have
• Something like this sample postcard:

```html
<!DOCTYPE html>
<html lang="en">
<head>
<meta charset="utf-8">
<title>Brightwick Music Studio – Postcard</title>
<link rel="stylesheet" href="https://fonts.googleapis.com/css2?family=Sorts+Mill+Goudy&family=Great+Vibes&family=Luckiest+Guy&family=Bebas+Neue&display=swap">
<style>
  :root {
    --page: #e9e7e4;
    --navy: #0c0e1d;
    --teal: #4fb8bd;
    --teal-bright: #5cc4c6;
    --white: #ffffff;
    --line: #c9c9c9;
    --ink: #1a1a1a;
    --photo-kids: #2c3050;
    --photo-kids-2: #4a4560;
    --photo-girl: #1f2024;
    --photo-girl-2: #1d3b37;
    --photo-dancer: #b8423a;
  }
  * { box-sizing: border-box; margin: 0; padding: 0; }
  html, body { width: 1200px; height: 698px; overflow: hidden; background: var(--page); }
  .stage { position: relative; width: 1200px; height: 698px; }
  .card {
    position: absolute; top: 149px; width: 479px; height: 400px; overflow: hidden;
    box-shadow: 0 4px 12px rgba(0,0,0,.25);
  }
  .card--front { left: 106px; background: var(--navy); }
  .card--back { left: 616px; background: var(--teal); }

  .photo { position: absolute; }
  .photo--students { left: 0; top: 0; width: 479px; height: 200px;
    background: linear-gradient(180deg, var(--photo-kids-2) 0%, var(--photo-kids) 70%, var(--navy) 100%); }
  .photo--violinist { left: 305px; top: 0; width: 174px; height: 400px;
    background: linear-gradient(90deg, rgba(31,32,36,0) 0%, var(--photo-girl) 22%, var(--photo-girl) 100%),
                linear-gradient(180deg, var(--photo-girl) 0%, var(--photo-girl) 60%, var(--photo-girl-2) 100%);
    background-blend-mode: normal; }
  .photo--violinist::after { content: ""; position: absolute; inset: 0;
    background: linear-gradient(180deg, rgba(29,59,55,0) 55%, rgba(29,59,55,.9) 100%); }
  .swoosh { position: absolute; left: 0; top: 0; }

  .brand { position: absolute; display: flex; align-items: center; gap: 12px; }
  .brand__dot { border-radius: 50%; flex: none; }
  .brand__name { font-family: "Sorts Mill Goudy", serif; font-weight: 400; line-height: 1; }
  .brand__name .studio { display: block; font-size: 11px; letter-spacing: 7px; margin-top: 6px; }

  .card--front .brand { left: 45px; top: 32px; }
  .card--front .brand__dot { width: 64px; height: 64px; background: var(--teal); }
  .card--front .brand__name { color: var(--teal-bright); font-size: 33px; }

  .headline { position: absolute; left: 45px; top: 228px; color: var(--teal-bright); font-weight: 400; }
  .headline__row { display: flex; align-items: baseline; }
  .headline__script { font-family: "Great Vibes", cursive; font-size: 68px; line-height: 1; }
  .headline__small { font-family: "Great Vibes", cursive; font-size: 32px; margin-left: 14px; line-height: 1; }
  .headline__block { display: block; font-family: "Luckiest Guy", "Arial Black", sans-serif; font-size: 50px; letter-spacing: 1px; line-height: 1; margin-top: 2px; }

  .body-shape { position: absolute; left: 0; top: 0; }
  .card--back .brand { left: 0; top: 38px; width: 195px; flex-direction: column; gap: 16px; text-align: center; }
  .card--back .brand__dot { width: 66px; height: 66px; background: var(--white); }
  .card--back .brand__name { color: var(--white); font-size: 35px; }
  .card--back .brand__name .studio { font-size: 11px; letter-spacing: 6px; margin-top: 8px; }
  .photo--dancer { left: 55px; top: 204px; width: 104px; height: 114px; border-radius: 4px;
    background: linear-gradient(180deg, #5a8f8f 0%, var(--photo-dancer) 45%, #8a3a36 100%); }

  .contact { position: absolute; left: 0; top: 322px; width: 195px; text-align: center; color: var(--white);
    font-family: "Bebas Neue", sans-serif; font-style: normal; }
  .contact__phone { display: inline-block; font-size: 27px; letter-spacing: .5px; line-height: 1;
    border-top: 1.5px solid var(--white); border-bottom: 1.5px solid var(--white); padding: 3px 4px 1px; }
  .contact__line { font-size: 11.5px; line-height: 1.3; text-transform: uppercase; white-space: nowrap; }
  .contact__line--first { margin-top: 6px; }

  .stamp { position: absolute; left: 390px; top: 37px; width: 50px; height: 50px; border: 1px solid var(--line); }
  .address { position: absolute; left: 276px; top: 104px; width: 164px; }
  .address__label { font-family: Arial, sans-serif; font-size: 9px; color: var(--ink); height: 12px; }
  .address__line { margin-left: 10px; height: 24px; border-bottom: 1px solid var(--line); }
  .address__line--first { height: 29px; }
</style>
</head>
<body>
<main class="stage">

  <section class="card card--front" aria-label="Postcard front">
    <div class="photo photo--students" role="img" aria-label="Photo of a group of young music students standing together"></div>
    <svg class="swoosh" width="479" height="400" viewBox="0 0 479 400" aria-hidden="true">
      <path d="M0 146 C90 186 220 200 340 190 L340 200 C220 214 80 200 0 158 Z" fill="var(--teal)"/>
      <path d="M0 158 C80 200 220 214 340 200 L340 400 L0 400 Z" fill="var(--navy)"/>
    </svg>
    <div class="photo photo--violinist" role="img" aria-label="Photo of a young girl in a velvet dress holding a violin and bow"></div>

    <div class="brand">
      <span class="brand__dot"></span>
      <span class="brand__name">Brightwick<span class="studio">MUSIC STUDIO</span></span>
    </div>

    <h1 class="headline">
      <span class="headline__row"><span class="headline__script">Music</span><span class="headline__small">is Fun</span></span>
      <span class="headline__block">FOR KIDS</span>
    </h1>
  </section>

  <section class="card card--back" aria-label="Postcard back">
    <svg class="body-shape" width="479" height="400" viewBox="0 0 479 400" aria-hidden="true">
      <path d="M282 0 H479 V400 H280 C210 388 165 335 167 275 C168 235 188 208 205 195 L205 150 C192 135 188 115 191 95 C196 45 235 8 282 0 Z" fill="var(--white)"/>
      <circle cx="196" cy="172" r="33" fill="var(--teal)"/>
    </svg>

    <div class="brand">
      <span class="brand__dot"></span>
      <span class="brand__name">Brightwick<span class="studio">MUSIC STUDIO</span></span>
    </div>

    <div class="photo photo--dancer" role="img" aria-label="Photo of a young girl in a red dress dancing with a violin"></div>

    <address class="contact">
      <span class="contact__phone">202-555-0147</span>
      <div class="contact__line contact__line--first">lessons@brightwickmusicstudio.example</div>
      <div class="contact__line">www.brightwickmusicstudio.example</div>
    </address>

    <div class="stamp" aria-label="Stamp area"></div>
    <div class="address">
      <div class="address__label">To</div>
      <div class="address__line address__line--first"></div>
      <div class="address__line"></div>
      <div class="address__line"></div>
      <div class="address__line"></div>
    </div>
  </section>

</main>
</body>
</html>
```